Bramblewood Joinery Website

My client Bramblewood Joinery is looking for a redesign for a Word Press Website. Their current site is at www.bramblewoodjoinery.example They are a custom cabinet company, but also create bathroom, living room, bar and entertainment and bedroom cabinets too. They would like a design that emulates the master craftsman work they do yet a contemporary style.

Their current site was designed using Flash elements.

Target Market(s)

Home owners and builders of high end homes

Industry/Entity Type

Entertainment

Font styles to use
Serif
Decorative

Requirements
Must have
• Must show their work and logo using a contemporary style.
Nice to have
• Sliders that showcase their projects.

```html
<!DOCTYPE html>
<html lang="en">
<head>
<meta charset="utf-8">
<title>Bramblewood Joinery</title>
<link rel="stylesheet" href="https://fonts.googleapis.com/css2?family=Raleway:wght@400;500;700&family=Open+Sans:wght@400;600&display=swap">
<style>
:root{
  --green:#2a9a2a;
  --link-green:#1e7d1e;
  --ink:#2b2b2b;
  --text:#3a3a3a;
  --muted:#777;
  --footer:#3a3839;
  --footer-text:#a9a7a8;
  --white:#fff;
  --rule:#d6d6d6;
}
*{margin:0;padding:0;box-sizing:border-box}
html,body{width:1020px;height:1200px;overflow:hidden;background:var(--white)}
body{position:relative;font-family:"Open Sans",Arial,sans-serif;color:var(--text)}
h1,h2,h3{font-weight:400}
.abs{position:absolute}

/* header */
.site-header{left:0;top:0;width:1020px;height:71px;background:var(--white)}
.brand{left:96px;top:18px;display:flex;align-items:center;gap:8px;font-family:"Raleway",sans-serif;font-weight:700;font-size:17px;color:var(--ink)}
.brand-dot{width:22px;height:22px;border-radius:50%;background:var(--green)}
.top-contact{top:15px;font-family:"Raleway",sans-serif;font-size:11.5px;color:var(--muted);display:flex;align-items:center;gap:6px}
.main-nav{left:282px;top:40px;display:flex;align-items:center;gap:15px;font-family:"Raleway",sans-serif;font-size:12px;font-weight:500;color:#444}

/* hero */
.hero{left:0;top:71px;width:1020px;height:408px;background:linear-gradient(180deg,#d9d6d0 0%,#c9c4bb 45%,#a88b68 80%,#8e6f4e 100%)}
.hero-panel{left:229px;top:207px;width:551px;height:158px;background:rgba(40,40,40,.82);text-align:center}
.hero-title{margin-top:15px;font-family:"Raleway",sans-serif;font-weight:500;font-size:29px;line-height:32px;color:var(--white)}
.hero-btn{position:absolute;left:208px;top:98px;width:126px;height:36px;border:1px solid var(--white);color:var(--white);font-family:"Raleway",sans-serif;font-size:14px;line-height:34px}
.dots{left:478px;top:436px;display:flex;gap:5px}
.dot{width:13px;height:13px;border-radius:50%;background:var(--white);border:1px solid #999}
.dot.on{background:#38b938;border-color:#38b938}

/* portfolio */
.section-title{top:517px;left:0;width:1020px;text-align:center;font-family:"Raleway",sans-serif;font-weight:400;font-size:31px;color:var(--ink);letter-spacing:.5px}
.section-title b{font-weight:700}
.title-rule{top:532px;height:4px;border-top:1px solid var(--rule);border-bottom:1px solid var(--rule)}
.card{top:586px;width:173px;height:220px;text-align:center}
.card-img{height:133px;position:relative}
.card-cap{position:absolute;left:0;bottom:0;width:100%;height:24px;background:rgba(35,35,35,.78);color:var(--white);font-family:"Raleway",sans-serif;font-weight:700;font-size:11.5px;line-height:24px}
.card-text{margin-top:9px;font-size:10.5px;line-height:15px;color:var(--ink);padding:0 3px}
.card-text.tight{margin-top:2px}
.card-more{position:absolute;top:201px;left:0;width:100%;font-size:9px;font-weight:600;color:var(--link-green)}

/* about + video */
.block-title{top:832px;font-family:"Raleway",sans-serif;font-weight:400;font-size:21px;color:var(--ink)}
.block-title b{font-weight:700}
.about-text{left:136px;top:869px;width:410px;height:152px;overflow:hidden;font-size:12px;line-height:17px;color:var(--text)}
.about-btn{left:136px;top:1037px;width:75px;height:25px;background:#151515;border-radius:2px;color:var(--white);font-size:10px;font-weight:600;line-height:25px;text-align:center;box-shadow:0 1px 2px rgba(0,0,0,.4)}
.video-frame{left:583px;top:869px;width:349px;height:200px;background:#d4d4d4;padding:6px}
.video-still{width:100%;height:100%;background:linear-gradient(135deg,#7d6d55 0%,#b5a68c 40%,#c9b8a0 70%,#8a7a63 100%);position:relative}
.video-bar{position:absolute;left:7px;right:7px;bottom:8px;height:18px;background:rgba(20,20,20,.8);display:flex;align-items:center;gap:8px;padding:0 6px}
.track{flex:1;height:5px;background:#555;position:relative}
.track i{position:absolute;left:0;top:0;height:5px;width:28%;background:#2a9ee0}

/* footer */
.site-footer{left:0;top:1085px;width:1020px;height:115px;background:var(--footer)}
.foot-links{left:89px;top:24px;font-family:"Raleway",sans-serif;font-size:12.5px;color:var(--footer-text);display:flex;gap:14px}
.foot-contact{top:24px;font-family:"Raleway",sans-serif;font-size:11.5px;color:#ccc;display:flex;align-items:center;gap:8px}
.foot-rule{left:89px;top:54px;width:833px;border-top:1px solid #555}
.copyright{left:89px;top:74px;font-family:"Raleway",sans-serif;font-size:10px;color:#ccc}
.social{top:67px;width:28px;height:28px;background:#a8a8a8;border-radius:2px}
</style>
</head>
<body>

<header class="site-header abs">
  <div class="brand abs"><span class="brand-dot"></span>Bramblewood Joinery</div>
  <div class="top-contact abs" style="left:646px">
    <svg width="12" height="12" viewBox="0 0 24 24"><path fill="#8a8a8a" d="M6.6 10.8a15.1 15.1 0 0 0 6.6 6.6l2.2-2.2c.3-.3.7-.4 1-.2 1.1.4 2.3.6 3.6.6.6 0 1 .4 1 1V20c0 .6-.4 1-1 1C10.6 21 3 13.4 3 4c0-.6.4-1 1-1h3.5c.6 0 1 .4 1 1 0 1.3.2 2.5.6 3.6.1.3 0 .7-.2 1z"/></svg>
    020 5550 1942
  </div>
  <div class="top-contact abs" style="left:763px">
    <svg width="13" height="10" viewBox="0 0 26 20"><rect width="26" height="20" fill="#8a8a8a"/><path d="M1 1l12 10L25 1" stroke="#fff" stroke-width="2" fill="none"/></svg>
    info@bramblewoodjoinery.example
  </div>
  <nav class="main-nav abs">
    <svg width="13" height="12" viewBox="0 0 26 24"><path fill="var(--green)" d="M13 1 1 12h4v11h6v-7h4v7h6V12h4z"/></svg>
    <span>Who We Are</span><span>Getting Started</span><span>Contact Us</span><span>Customer Experience</span><span>Professional</span><span>Portfolio</span><span>Cabinet Hardware</span>
  </nav>
</header>

<section class="hero abs" role="img" aria-label="Bright white custom kitchen with grey counters, bar stools and wood floor"></section>
<div class="hero-panel abs">
  <h1 class="hero-title">Kansas City's Premier Custom<br>KitchenCabinet Design Company</h1>
  <div class="hero-btn">Read More</div>
</div>
<div class="dots abs"><span class="dot"></span><span class="dot on"></span><span class="dot"></span></div>

<div class="title-rule abs" style="left:92px;width:278px"></div>
<div class="title-rule abs" style="left:640px;width:283px"></div>
<h2 class="section-title abs">OUR <b>PORTFOLIO</b></h2>

<article class="card abs" style="left:133px">
  <div class="card-img" role="img" aria-label="White kitchen with range hood and pendant lights" style="background:linear-gradient(180deg,#8a7b6a,#d9d4cc 60%,#5a4a3b)"><div class="card-cap">LOREM IPSUM DOLOR SI</div></div>
  <p class="card-text">Lorem ipsum dolor sit amet, consectetur adipiscing elit, sed do eiusmod tempor</p>
  <div class="card-more">Read More &gt;&gt;</div>
</article>
<article class="card abs" style="left:323px">
  <div class="card-img" role="img" aria-label="Dark wood kitchen island on hardwood floor" style="background:linear-gradient(180deg,#c9b59a,#3a2a22 55%,#4a3020)"><div class="card-cap">LOREM IPSUM DOLOR SI</div></div>
  <p class="card-text">Lorem ipsum dolor sit amet, consectetur adipiscing elit, sed do eiusmod tempor</p>
  <div class="card-more">Read More &gt;&gt;</div>
</article>
<article class="card abs" style="left:513px">
  <div class="card-img" role="img" aria-label="White cabinetry with built-in steel oven" style="background:linear-gradient(180deg,#d8cdbd,#8c8c88 45%,#e6e2dc 70%,#5a3a25)"><div class="card-cap">LOREM IPSUM DOLOR SI</div></div>
  <p class="card-text">Lorem ipsum dolor sit amet, consectetur adipiscing elit, sed do eiusmod tempor</p>
  <div class="card-more">Read More &gt;&gt;</div>
</article>
<article class="card abs" style="left:703px">
  <div class="card-img" role="img" aria-label="Cream kitchen with glass-front cabinets and pendant lamps" style="background:linear-gradient(180deg,#7a6a55,#d9d2c4 55%,#2e2a26)"><div class="card-cap">LOREM IPSUM DOLOR SI</div></div>
  <p class="card-text tight">Lorem ipsum dolor sit amet, consectetur adipiscing elit, sed do eiusmod tempor</p>
  <div class="card-more">Read More &gt;&gt;</div>
</article>

<h3 class="block-title abs" style="left:136px">About <b>US</b></h3>
<p class="about-text abs">Established in 1966, Bramblewood Joinery has long stood as one of the Midwest's most renowned makers of custom cabinets and fixtures. Our handcrafted, award-winning creations have been chosen by hundreds of noteworthy homebuilders.<br>And while we custom build cabinets, we built our business around the belief that our customers absolutely, unequivocally come first.From day one, our mission has been to help turn the houses that people live in to the homes they've always dreamed of.Beyond new homebuilders, everyone from remodelers to commercial clients have benefitted from</p>
<div class="about-btn abs">Read More</div>

<h3 class="block-title abs" style="left:582px">Watch <b>Our Video</b></h3>
<div class="video-frame abs">
  <div class="video-still" role="img" aria-label="Craftsman cutting timber on a workshop table saw">
    <div class="video-bar">
      <svg width="10" height="10" viewBox="0 0 10 10"><path d="M1 0l9 5-9 5z" fill="#fff"/></svg>
      <div class="track"><i></i></div>
      <span style="font-size:8px;font-weight:600;color:#2a9ee0">HD</span>
    </div>
  </div>
</div>

<footer class="site-footer abs">
  <div class="foot-links abs"><span>Advice</span><span>|</span><span>About</span><span>|</span><span>Contact</span><span>|</span><span>Privacy Policy</span><span>|</span><span>Terms &amp; Conditons</span></div>
  <div class="foot-contact abs" style="left:631px">
    <svg width="14" height="14" viewBox="0 0 24 24"><path fill="#a8a8a8" d="M6.6 10.8a15.1 15.1 0 0 0 6.6 6.6l2.2-2.2c.3-.3.7-.4 1-.2 1.1.4 2.3.6 3.6.6.6 0 1 .4 1 1V20c0 .6-.4 1-1 1C10.6 21 3 13.4 3 4c0-.6.4-1 1-1h3.5c.6 0 1 .4 1 1 0 1.3.2 2.5.6 3.6.1.3 0 .7-.2 1z"/></svg>
    816.555.0148
  </div>
  <div class="foot-contact abs" style="left:755px">
    <svg width="14" height="11" viewBox="0 0 26 20"><rect width="26" height="20" fill="#a8a8a8"/><path d="M1 1l12 10L25 1" stroke="#3a3839" stroke-width="2" fill="none"/></svg>
    info@bramblewoodjoinery.example
  </div>
  <div class="foot-rule abs"></div>
  <p class="copyright abs">Copyright © 2015 Bramblewood Joinery. All Rights Reserved</p>
  <span class="social abs" style="left:793px" aria-label="Social link"></span>
  <span class="social abs" style="left:837px" aria-label="Social link"></span>
  <span class="social abs" style="left:881px" aria-label="Social link"></span>
</footer>

</body>
</html>
```